Private Investment Firm Needs PowerPoint Presentation Template

Design PowerPoint template, take Pinebrook-submitted rough presentation draft, and drop it into new template. See attached Project Brief file for more detail.
Updates

Some decent designs have been submitted but they seem to lack the understanding of our target markets. I am hopeful that more time and feedback will result in better results.

Target Market(s)

Private company owners and intermediaries.

Font styles to use
Serif

Colors
3176b5

Requirements
Must have
• See attached Project Brief.
Nice to have
Should not have
• No B2C fluff--this is a B2B project.

```html
<!DOCTYPE html>
<html lang="en">
<head>
<meta charset="utf-8">
<title>Introduction to Non-Control Capital</title>
<link rel="stylesheet" href="https://fonts.googleapis.com/css2?family=Cinzel:wght@700&family=Montserrat:wght@400;600&family=Roboto:wght@700&display=swap">
<style>
  :root {
    --brand-blue: #1a72b9;
    --band-blue-top: #0f6cb8;
    --band-blue-bottom: #3b9bd2;
    --band-grey: #555555;
    --text-grey: #5f5f5f;
    --ink: #3a3a3a;
    --paper: #ffffff;
    --paper-shade: #eef0f2;
  }
  * { margin: 0; padding: 0; box-sizing: border-box; }
  html, body { width: 1200px; height: 675px; overflow: hidden; }
  body { background: var(--paper); }
  .slide {
    position: relative;
    width: 1200px;
    height: 675px;
    overflow: hidden;
    background: radial-gradient(ellipse at 75% 20%, var(--paper) 45%, var(--paper-shade) 100%);
  }
  .slide__bands { position: absolute; inset: 0; }
  .slide__content { position: absolute; inset: 0; text-align: center; }
  .title {
    position: absolute;
    top: 109px;
    left: 0; right: 0;
    font-family: "Cinzel", serif;
    font-weight: 700;
    font-size: 58px;
    line-height: 64px;
    color: var(--brand-blue);
    letter-spacing: 0.5px;
  }
  .subtitle {
    position: absolute;
    top: 273px;
    left: 0; right: 0;
    font-family: "Montserrat", sans-serif;
    font-weight: 400;
    font-size: 17.5px;
    line-height: 26px;
    color: var(--text-grey);
    letter-spacing: 0.6px;
  }
  .subtitle strong {
    font-family: "Roboto", sans-serif;
    font-weight: 700;
    color: var(--brand-blue);
    letter-spacing: 0.3px;
  }
  .edition {
    position: absolute;
    left: 463px;
    top: 388px;
    width: 274px;
    height: 70px;
    border: 1px solid #6a6a6a;
    font-family: "Montserrat", sans-serif;
    font-weight: 400;
    font-size: 38px;
    line-height: 68px;
    color: var(--ink);
  }
  .brand {
    position: absolute;
    top: 515px;
    left: 0; right: 0;
    display: flex;
    justify-content: center;
    align-items: center;
    gap: 14px;
  }
  .brand__dot {
    width: 58px; height: 58px;
    border-radius: 50%;
    background: var(--brand-blue);
  }
  .brand__name {
    font-family: "Montserrat", sans-serif;
    font-weight: 600;
    font-size: 23px;
    line-height: 58px;
    color: var(--ink);
  }
  .website {
    position: absolute;
    top: 618px;
    left: 0; right: 0;
    font-family: "Montserrat", sans-serif;
    font-weight: 400;
    font-size: 26px;
    color: var(--ink);
  }
  .website strong { font-weight: 600; color: var(--brand-blue); }
</style>
</head>
<body>
<main class="slide">
  <svg class="slide__bands" width="1200" height="675" viewBox="0 0 1200 675" aria-hidden="true">
    <defs>
      <linearGradient id="blueBand" x1="0" y1="0" x2="0" y2="1">
        <stop offset="0" style="stop-color:#0f6cb8"/>
        <stop offset="1" style="stop-color:#3b9bd2"/>
      </linearGradient>
    </defs>
    <polygon points="0,0 120,0 0,496" fill="#555555"/>
    <polygon points="1164,0 1200,0 1200,675 950,675" fill="url(#blueBand)"/>
  </svg>

  <div class="slide__content">
    <h1 class="title">Introduction to<br>Non-Control Capital</h1>
    <p class="subtitle">The Lower Middle Market Private company Strategy for<br>Raising Capital While <strong>Maintaining Business Control</strong></p>
    <div class="edition">Fall-2018</div>
    <div class="brand">
      <span class="brand__dot"></span>
      <span class="brand__name">Pinebrook Capital</span>
    </div>
    <p class="website">www.<strong>pinebrookcapital</strong>.com</p>
  </div>
</main>
</body>
</html>
```